Brimsett Gardening Fresh New Website

We are looking to create a simple fresh website for our landscaping business. The website should appeal to a 'high end' audience. We deal with a lot of Embassies and affluent clients who have extremely large gardens that are meticulously maintained. The site is about communicating our excellent landscaping and customer service skills and encouraging new clients to reach out and engage us to take care of their gardens.

The website is basically going to be our business card, it will have almost no functionality other than two 'contact us' forms, one for smaller clients and one for more detailed projects.

The website will not have a lot of written content and will have to show photos of beautifully landscaped gardens.

The main logo in black will influence the site, however, we are open to all suggestions.

We are expecting to have the following pages:
Home Page
Services
About Us
Contact Us
Showcase (photo gallery of our work)

We need someone who can code it to wordpress and be available for minor changes over a number of days. They will be simple tweaks.

```html
<!DOCTYPE html>
<html lang="en">
<head>
<meta charset="utf-8">
<title>Brimsett Gardening</title>
<link href="https://fonts.googleapis.com/css2?family=Libre+Baskerville:wght@400;700&family=Lato:wght@400;700&display=swap" rel="stylesheet">
<style>
:root{
  --black:#000;
  --ink:#111;
  --text:#555;
  --gold:#c9a227;
  --gold-light:#e6c23c;
  --gold-dark:#a9791c;
  --gold-grad:linear-gradient(180deg,#e3bd35 0%,#b9881f 100%);
  --white:#fff;
  --line:#e8e8e8;
}
*{margin:0;padding:0;box-sizing:border-box}
html,body{width:1200px;height:4222px;overflow:hidden}
body{font-family:"Lato",sans-serif;color:var(--text);background:var(--white);position:relative}
.serif{font-family:"Libre Baskerville",serif;font-weight:700;color:var(--ink)}
.btn{position:absolute;display:flex;align-items:center;justify-content:center;border-radius:20px;font-size:15px;font-weight:700;color:var(--ink);background:var(--gold-grad)}
.btn.light{background:var(--white);color:var(--gold-dark)}
.photo{position:absolute;overflow:hidden}

/* header */
.site-header{position:absolute;left:0;top:0;width:1200px;height:151px;background:var(--black);border-bottom:1px solid #333}
.brand{position:absolute;display:flex;align-items:center;justify-content:center;gap:10px;font-family:"Lato",sans-serif;font-weight:700;font-size:17px;color:var(--gold);white-space:nowrap}
.brand .mark{width:12px;height:12px;border-radius:50%;background:var(--gold)}
.contact-item{position:absolute;top:30px;display:flex;align-items:center;gap:14px}
.contact-item .dot{width:38px;height:38px;border-radius:50%;background:var(--gold-grad);display:flex;align-items:center;justify-content:center}
.contact-item .label{font-family:"Libre Baskerville",serif;font-size:15px;color:var(--gold-light);font-weight:400}
.contact-item .value{font-size:13px;color:var(--white);margin-top:6px}
.main-nav a{position:absolute;top:106px;font-size:14px;color:var(--white);text-decoration:none}

/* hero */
.hero{position:absolute;left:0;top:151px;width:1200px;height:647px;background:radial-gradient(circle at 85% 35%,#6b6226 0%,transparent 25%),linear-gradient(160deg,#1a2410 0%,#2d3d18 40%,#3e5420 65%,#1e2710 100%)}
.hero h1{position:absolute;left:112px;top:148px;font-size:62px;line-height:86px;color:var(--white);white-space:nowrap}
.hero p{position:absolute;left:112px;top:327px;width:620px;font-size:17px;line-height:32px;color:var(--white)}

/* about */
.about h2{position:absolute;left:112px;top:888px;font-size:41px;line-height:66px}
.about .rule{position:absolute;left:455px;top:872px;width:2px;height:223px;background:var(--gold)}
.about p{position:absolute;left:513px;top:875px;width:580px;font-size:15px;line-height:31.5px}

/* appointment */
.appt{position:absolute;left:734px;top:1160px;width:353px;height:447px;background:linear-gradient(180deg,#e5bd2f 0%,#b98a1f 100%);box-shadow:0 4px 14px rgba(0,0,0,.18);text-align:center;color:var(--white)}
.appt h3{font-family:"Libre Baskerville",serif;font-size:30px;line-height:44px;margin-top:22px}
.appt p{font-size:12.5px;line-height:22px;margin:8px 24px 0}
.field{position:absolute;background:var(--white);font-size:11.5px;color:#777;padding:0 14px;display:flex;align-items:center}
.field.tall{align-items:flex-start;padding-top:12px}

/* sections */
.section-title{position:absolute;left:0;width:1200px;text-align:center}
.section-lead{position:absolute;left:190px;width:820px;text-align:center;font-size:14.5px;line-height:32px}
.feature{position:absolute;width:473px;height:183px;border:1px solid var(--line);border-radius:4px 40px 4px 40px;background:var(--white)}
.feature svg{position:absolute;left:20px;top:38px}
.feature h4{position:absolute;left:98px;top:38px;font-family:"Libre Baskerville",serif;font-size:15px;color:var(--ink);white-space:nowrap}
.feature p{position:absolute;left:98px;top:70px;width:355px;font-size:13px;line-height:27px}

.portfolio{position:absolute;left:0;top:2331px;width:1200px;height:934px;background:radial-gradient(circle at 50% 40%,#2e3e18 0%,#17200c 70%,#0f150a 100%)}

.pill{position:absolute;left:177px;width:403px;height:54px;border-radius:27px;background:var(--white);box-shadow:0 2px 12px rgba(0,0,0,.09);font-size:13px;color:#666;padding-left:32px;display:flex;align-items:center}

/* footer */
.site-footer{position:absolute;left:0;top:3880px;width:1200px;height:342px;background:linear-gradient(180deg,#0c0c0c,#161616)}
.foot-nav a{position:absolute;top:4070px;font-size:16px;color:var(--white);text-decoration:none;transform:translateX(-50%)}
.social{position:absolute;top:4124px;width:36px;height:36px;border-radius:50%;background:var(--gold-grad);display:flex;align-items:center;justify-content:center}
</style>
</head>
<body>

<header class="site-header">
  <div class="brand" style="left:88px;top:62px;width:180px"><span class="mark"></span>Brimsett Gardening</div>
  <div class="contact-item" style="left:423px">
    <span class="dot"><svg width="14" height="18" viewBox="0 0 14 18"><path d="M7 0C3 0 0 3 0 7c0 5 7 11 7 11s7-6 7-11c0-4-3-7-7-7z" fill="#fff"/><circle cx="7" cy="7" r="2.5" fill="#c9a227"/></svg></span>
    <div><div class="label">Location</div><div class="value">Brimsett Gardening, USA</div></div>
  </div>
  <div class="contact-item" style="left:656px">
    <span class="dot"><svg width="18" height="13" viewBox="0 0 18 13"><rect width="18" height="13" rx="2" fill="#fff"/><path d="M1 1l8 6 8-6" stroke="#c9a227" stroke-width="1.6" fill="none"/></svg></span>
    <div><div class="label">Email Address</div><div class="value">hello@brimsettgardening.com</div></div>
  </div>
  <div class="contact-item" style="left:912px">
    <span class="dot"><svg width="16" height="16" viewBox="0 0 16 16"><path d="M3 1l3 3-2 2c1 2 3 4 5 5l2-2 3 3-2 3C6 15 1 10 0 3z" fill="#fff"/></svg></span>
    <div><div class="label">Contact Number</div><div class="value">+1 555 014 2290</div></div>
  </div>
  <nav class="main-nav">
    <a style="left:562px">Home</a>
    <a style="left:654px">About Us</a>
    <a style="left:767px">Our Services</a>
    <a style="left:903px">Portfolio</a>
    <a style="left:1013px">Contact Us</a>
  </nav>
</header>

<section class="hero" role="img" aria-label="Garden path at dusk with lit bollard lamps and manicured lawn">
  <h1 class="serif">WELCOME TO<br>BRIMSETT GARDENING</h1>
  <p>Et harum quidem rerum facilis est et expedita distinctio. Nam libero tempore, cum soluta nobis est eligendi optio cumque nihil impedit quo minus id quod maxime placeat facere possimus, omnis voluptas</p>
  <span class="btn" style="left:112px;top:450px;width:134px;height:36px">Get Started</span>
  <span class="btn" style="left:262px;top:450px;width:210px;height:36px">Make An Appointment</span>
</section>

<section class="about">
  <h2 class="serif">ABOUT<br>BRIMSETT<br>GARDENING</h2>
  <div class="rule"></div>
  <p>On the other hand, we denounce with righteous indignation and dislike men who are so beguiled and demoralized by the charms of pleasure of the moment, so blinded by desire, that they cannot foresee the pain and trouble that are bound to ensue; and equal blame belongs to those who fail in their duty through weakness of will, which is the same as saying through shrinking from toil</p>
  <span class="btn" style="left:513px;top:1049px;width:120px;height:36px;font-size:14px">Read More</span>
</section>

<div class="photo" style="left:112px;top:1160px;width:339px;height:446px;background:linear-gradient(170deg,#4f8a1f 0%,#6a3a22 45%,#8a8270 65%,#5c9a25 100%)" role="img" aria-label="Landscaped garden bed with rocks, red mulch and stone path"></div>
<div class="photo" style="left:462px;top:1160px;width:256px;height:446px;background:radial-gradient(circle at 65% 50%,#5e9a2a 0%,#2f5a14 50%,#8ab840 100%)" role="img" aria-label="Clipped round boxwood shrub on a lawn"></div>

<form class="appt">
  <h3>MAKE AN<br>APPOINTMENT</h3>
  <p>Placeat facere possimus, omnis voluptas assumenda est, omnis dolor repellendus.</p>
  <span class="field" style="left:25px;top:179px;width:144px;height:34px">Full Name</span>
  <span class="field" style="left:184px;top:179px;width:144px;height:34px">Email Address</span>
  <span class="field" style="left:25px;top:227px;width:144px;height:34px">Contact Number</span>
  <span class="field" style="left:184px;top:227px;width:144px;height:34px;justify-content:space-between">Choose Service<svg width="8" height="5" viewBox="0 0 8 5"><path d="M1 1l3 3 3-3" stroke="#777" fill="none"/></svg></span>
  <span class="field tall" style="left:25px;top:274px;width:303px;height:87px">Message......</span>
  <span class="btn light" style="left:90px;top:381px;width:173px;height:36px;font-size:13px">Make An Appointment</span>
</form>

<h2 class="serif section-title" style="top:1697px;font-size:42px">WHY CHOOSE US</h2>
<p class="section-lead" style="top:1769px">Blinded by desire, that they cannot foresee the pain and trouble that are bound to ensue; and equal blame belongs to those who fail in their duty through weakness of will, which is the same as saying through shrinking from toil and pain.</p>

<div class="feature" style="left:112px;top:1868px">
  <svg width="60" height="50" viewBox="0 0 60 50" fill="none" stroke="#c9a227" stroke-width="2"><circle cx="18" cy="18" r="12"/><circle cx="40" cy="22" r="10"/><path d="M18 30v16M40 32v14M4 46h52"/></svg>
  <h4>BLINDED BY DESIRE CANNOT FORESEE</h4>
  <p>Duty through weakness of will, which is the same as saying through shrinking from toil and pain. These cases are perfectly simple and easy to distinguish. In a free</p>
</div>
<div class="feature" style="left:615px;top:1868px">
  <svg width="60" height="50" viewBox="0 0 60 50" fill="none" stroke="#c9a227" stroke-width="2"><path d="M30 46V24M30 30c-10 0-14-8-14-12 8 0 14 4 14 12zM30 26c8 0 12-6 12-10-6 0-12 3-12 10zM8 46h44"/></svg>
  <h4>BLINDED BY DESIRE CANNOT FORESEE</h4>
  <p>Duty through weakness of will, which is the same as saying through shrinking from toil and pain. These cases are perfectly simple and easy to distinguish. In a free</p>
</div>
<div class="feature" style="left:112px;top:2073px">
  <svg width="60" height="56" viewBox="0 0 60 56" fill="none" stroke="#c9a227" stroke-width="2"><path d="M20 4l10 24M40 4L30 28"/><circle cx="22" cy="40" r="8"/><circle cx="38" cy="40" r="8"/></svg>
  <h4>BLINDED BY DESIRE CANNOT FORESEE</h4>
  <p>Duty through weakness of will, which is the same as saying through shrinking from toil and pain. These cases are perfectly simple and easy to distinguish. In a free</p>
</div>
<div class="feature" style="left:615px;top:2073px">
  <svg width="60" height="50" viewBox="0 0 60 50" fill="none" stroke="#c9a227" stroke-width="2"><path d="M18 46V28M18 32c-7 0-10-6-10-9 6 0 10 3 10 9zM42 46V24M42 28c7 0 10-6 10-9-6 0-10 3-10 9zM6 46h48"/><circle cx="30" cy="10" r="5"/></svg>
  <h4>BLINDED BY DESIRE CANNOT FORESEE</h4>
  <p>Duty through weakness of will, which is the same as saying through shrinking from toil and pain. These cases are perfectly simple and easy to distinguish. In a free</p>
</div>

<section class="portfolio" role="img" aria-label="Aerial view of a formal garden, darkened">
  <h2 class="serif section-title" style="top:70px;font-size:42px;color:#fff">OUR PORTFOLIO</h2>
  <p class="section-title" style="top:140px;font-size:16px;color:#fff">Et harum quidem rerum facilis est et expedita distinctio. Nam libero tempore, cum soluta nobis est eligendi</p>
</section>
<div class="photo" style="left:112px;top:2547px;width:316px;height:349px;border-radius:16px;background:linear-gradient(150deg,#1d2a14 0%,#4e6a22 45%,#4a8aa0 90%)" role="img" aria-label="Garden lights along a blue stone path at dusk"></div>
<div class="photo" style="left:112px;top:2926px;width:316px;height:195px;border-radius:16px;background:linear-gradient(180deg,#6fa830 0%,#8a8a80 50%,#4a9ab0 100%)" role="img" aria-label="Rock-edged pond with lavender planting"></div>
<div class="photo" style="left:443px;top:2547px;width:314px;height:195px;border-radius:16px;background:linear-gradient(160deg,#4a6a2a 0%,#62b226 55%,#b0b0a8 100%)" role="img" aria-label="Curved paver walkway through a green lawn"></div>
<div class="photo" style="left:443px;top:2772px;width:314px;height:349px;border-radius:16px;background:linear-gradient(180deg,#3a4a22 0%,#5a7a24 40%,#8e8e86 75%,#4a6a20 100%)" role="img" aria-label="Gravel bed with shrubs and ornamental grasses"></div>
<div class="photo" style="left:772px;top:2547px;width:315px;height:349px;border-radius:16px;background:linear-gradient(180deg,#7ab0e0 0%,#c8dcef 25%,#3c6a22 45%,#5aa62a 75%,#4c8e20 100%)" role="img" aria-label="Striped lawn with trees under a blue sky"></div>
<div class="photo" style="left:772px;top:2926px;width:315px;height:195px;border-radius:16px;background:linear-gradient(180deg,#3a5a20 0%,#7a9a4a 50%,#c0b8a8 80%,#5a9a28 100%)" role="img" aria-label="Flowering borders along a garden path"></div>
<span class="btn light" style="left:439px;top:3152px;width:118px;height:36px;font-size:14px">View More</span>
<span class="btn light" style="left:574px;top:3152px;width:186px;height:36px;font-size:14px">Make An Appointment</span>

<h2 class="serif section-title" style="top:3338px;font-size:42px">GET IN TOUCH WITH US</h2>
<p class="section-lead" style="top:3409px">Blinded by desire, that they cannot foresee the pain and trouble that are bound to ensue; and equal blame belongs to those who fail in their duty through weakness of will, which is the same as saying through shrinking from toil and pain.</p>
<span class="pill" style="top:3516px">Full Name</span>
<span class="pill" style="top:3588px">Email Address</span>
<span class="pill" style="top:3660px">Contact Number</span>
<span class="btn" style="left:177px;top:3734px;width:403px;height:54px;border-radius:27px;font-size:16px;box-shadow:0 3px 10px rgba(0,0,0,.18)">Submit Here</span>
<span class="pill" style="left:616px;top:3516px;width:405px;height:272px;border-radius:24px;align-items:flex-start;padding-top:20px">Your Message Goes Here....</span>

<footer class="site-footer"></footer>
<div class="brand" style="left:500px;top:4010px;width:200px"><span class="mark"></span>Brimsett Gardening</div>
<nav class="foot-nav">
  <a style="left:238px">Home</a>
  <a style="left:351px">About Us</a>
  <a style="left:472px">Services</a>
  <a style="left:592px">Portfolio</a>
  <a style="left:721px">Contact Us</a>
  <a style="left:900px">Make An Appointment</a>
</nav>
<span class="social" style="left:513px" aria-label="Email"><svg width="16" height="12" viewBox="0 0 16 12"><rect x="1" y="1" width="14" height="10" rx="1.5" fill="none" stroke="#111" stroke-width="1.5"/><path d="M1.5 1.5l6.5 5 6.5-5" fill="none" stroke="#111" stroke-width="1.5"/></svg></span>
<span class="social" style="left:559px" aria-label="Phone"><svg width="14" height="14" viewBox="0 0 16 16"><path d="M3 1l3 3-2 2c1 2 3 4 5 5l2-2 3 3-2 3C6 15 1 10 0 3z" fill="#111"/></svg></span>
<span class="social" style="left:605px" aria-label="Location"><svg width="12" height="16" viewBox="0 0 14 18"><path d="M7 0C3 0 0 3 0 7c0 5 7 11 7 11s7-6 7-11c0-4-3-7-7-7z" fill="#111"/><circle cx="7" cy="7" r="2.5" fill="#d4ac2c"/></svg></span>
<span class="social" style="left:649px" aria-label="Link"><svg width="16" height="16" viewBox="0 0 16 16" fill="none" stroke="#111" stroke-width="1.8"><path d="M7 9l2-2"/><rect x="1.5" y="7" width="7" height="4.5" rx="2.2" transform="rotate(-45 5 9.25)"/><rect x="7.5" y="4.5" width="7" height="4.5" rx="2.2" transform="rotate(-45 11 6.75)"/></svg></span>
<p class="section-title" style="top:4180px;font-size:11px;color:#fff">(C) Copyright 2024 | All Rights Reserved.</p>

</body>
</html>
```